Vibrant, yet professional, stationery set and other designs required.

I need to source a fantastic designer for a new project as part of my company using a new logo designed via sketch harbor.

**UPDATE** I am not looking for just 'fine' design that will suffice. I am looking for something great.

We are a life assurance brokerage based in Dublin, Ireland and BrightRoost.ie is our new website aimed at providing services for young families in Ireland. We are hoping to be the 'Velro' level of service providers in this area and I am looking for the quality of design to reflect this :-) Hopefully that makes sense!

I have a preference for straight lines over curves and waves.

I need...

1. Business card
2. Letterhead
3. Banner (for printing - 76cm X 305cm)
4. Car branding for KORVA 9 (2014 sport model) I believe the templates are freely available online.

Target Market(s)

Parents in Ireland - Aged 27 to 50.

Industry/Entity Type

Financial Planning

Colors

Designer to choose colors to be used in the design.

Requirements
Must have
• All of the items listed in the description above. I like clean, bright, legible, vibrant and professional design.
Should not have
• No silly or 'cheap' looking designs. This is a professional company looking to provide a professional service.

```html
<!DOCTYPE html>
<html lang="en">
<head>
<meta charset="utf-8">
<title>BrightRoost.ie – Business Card</title>
<link rel="stylesheet" href="https://fonts.googleapis.com/css2?family=Roboto:wght@400;500&display=swap">
<style>
  :root {
    --backdrop: #e2e2e2;
    --card-front: #f7f7f7;
    --card-back: #8e9a9d;
    --brand-grey: #8a9599;
    --accent-green: #8dc63f;
    --text-dark: #4a4f52;
    --rule: #c9cdcf;
    --white: #ffffff;
  }
  html, body {
    margin: 0;
    padding: 0;
    width: 1200px;
    height: 960px;
    overflow: hidden;
    background: var(--backdrop);
    font-family: "Roboto", Arial, sans-serif;
  }
  .canvas {
    position: relative;
    width: 1200px;
    height: 960px;
  }
  .card {
    position: absolute;
    width: 600px;
    height: 341px;
    box-sizing: border-box;
  }
  .card--front {
    left: 302px;
    top: 130px;
    background: var(--card-front);
    border: 1px solid #d6d6d6;
  }
  .card--back {
    left: 300px;
    top: 489px;
    background: var(--card-back);
  }
  .brand-name {
    position: absolute;
    margin: 0;
    font-weight: 500;
    letter-spacing: -0.5px;
    white-space: nowrap;
  }
  .card--front .brand-name {
    left: 58px;
    top: 155px;
    font-size: 38px;
    line-height: 1;
    color: var(--brand-grey);
  }
  .card--back .brand-name {
    left: 0;
    width: 600px;
    text-align: center;
    top: 140px;
    font-size: 58px;
    line-height: 1;
    color: var(--white);
  }
  .divider {
    position: absolute;
    left: 319px;
    top: 83px;
    width: 1px;
    height: 182px;
    background: var(--rule);
  }
  .contact {
    position: absolute;
    left: 347px;
    top: 78px;
    color: var(--text-dark);
    font-size: 14.5px;
    line-height: 19.3px;
  }
  .contact__name {
    margin: 0;
    font-size: 21px;
    line-height: 24px;
    font-weight: 500;
    color: var(--accent-green);
  }
  .contact__role {
    margin: 0 0 10px;
    font-size: 14.5px;
    line-height: 18px;
    font-weight: 500;
    color: var(--brand-grey);
  }
  .contact__address,
  .contact__lines {
    margin: 0;
    font-style: normal;
  }
  .contact__address { margin-bottom: 6px; }
</style>
</head>
<body>
<main class="canvas">
  <section class="card card--front" aria-label="Business card front">
    <p class="brand-name">BrightRoost.ie</p>
    <div class="divider"></div>
    <div class="contact">
      <h1 class="contact__name">OWEN HARTLEY</h1>
      <p class="contact__role">CEO/FOUNDER</p>
      <address class="contact__address">4120 Larkfield Row<br>Millbrook, Dublin 20418</address>
      <p class="contact__lines">
        (P) 614 208 3371<br>
        (C) 852 719 4406<br>
        (F) 473 560 1182<br>
        owen@brightroost.com<br>
        www.brightroost.com
      </p>
    </div>
  </section>

  <section class="card card--back" aria-label="Business card back">
    <p class="brand-name">BrightRoost.ie</p>
  </section>
</main>
</body>
</html>
```